KLV Plant Services

We are a heavy diesel mechanical business with additional air con certificates, remapping engine rebuilt

Contact Information for Business Card

Company Name, Director Name, Managing Director, Contact details, email and website

Font styles to use
Serif
Script

```html
<!DOCTYPE html>
<html lang="en">
<head>
<meta charset="utf-8">
<title>KLV Plant Services – Business Card</title>
<link rel="stylesheet" href="https://fonts.googleapis.com/css2?family=Great+Vibes&family=Lora:wght@700&family=Poppins:wght@400&display=swap">
<style>
  :root {
    --navy: #0b0a78;
    --navy-back: #0c0b82;
    --ink: #1a1a1a;
    --paper: #ffffff;
    --stage: #d6d6d6;
    --font-serif: "Lora", Georgia, serif;
    --font-script: "Great Vibes", cursive;
    --font-body: "Poppins", sans-serif;
  }
  * { box-sizing: border-box; margin: 0; padding: 0; }
  html, body { width: 1200px; height: 965px; overflow: hidden; }
  body {
    background: var(--stage);
    font-family: var(--font-body);
    position: relative;
  }
  .card {
    position: absolute;
    top: 159px;
    width: 383px;
    height: 669px;
  }
  .card--front { left: 186px; background: var(--paper); }
  .card--back  { left: 653px; background: var(--navy-back); }

  .brand {
    position: absolute;
    left: 0; right: 0;
    text-align: center;
    font-family: var(--font-serif);
    font-weight: 700;
  }
  .card--front .brand {
    top: 96px;
    font-size: 36px;
    line-height: 1.15;
    color: var(--navy);
  }
  .card--back .brand {
    top: 319px;
    font-size: 14px;
    line-height: 1.2;
    color: var(--paper);
  }

  .person {
    position: absolute;
    top: 358px;
    left: 0; right: 0;
    text-align: center;
  }
  .person__name {
    font-family: var(--font-serif);
    font-weight: 700;
    font-size: 25px;
    color: var(--navy);
    letter-spacing: 0.5px;
    line-height: 32px;
  }
  .person__role {
    font-family: var(--font-script);
    font-size: 24px;
    color: var(--ink);
    line-height: 26px;
  }

  .icon-row {
    position: absolute;
    top: 0;
    left: 0;
  }

  .contact {
    position: absolute;
    top: 466px;
    left: 0; right: 0;
    text-align: center;
    font-size: 16px;
    line-height: 20px;
    color: var(--ink);
  }
  .divider {
    position: absolute;
    top: 548px;
    left: 49px;
    width: 285px;
    height: 2px;
    background: var(--navy);
  }
  .address {
    position: absolute;
    top: 569px;
    left: 0; right: 0;
    text-align: center;
    font-size: 16px;
    line-height: 20px;
    color: var(--ink);
  }
</style>
</head>
<body>

  <section class="card card--front" aria-label="Business card front">
    <div class="brand">KLV<br>Plant Services</div>

    <div class="person">
      <div class="person__name">MARK ELLISON</div>
      <div class="person__role">Director</div>
    </div>

    <svg class="icon-row" width="383" height="669" viewBox="0 0 383 669" aria-hidden="true">
      <path d="M49 438 L144 436 L144 438 Z" fill="var(--navy)"/>
      <path d="M238 436 L333 437 L238 438 Z" fill="var(--navy)"/>
      <rect x="151" y="427" width="20" height="20" fill="var(--navy)"/>
      <path d="M157 431 l2.5 0 l1 3 l-1.5 1.2 q1 2.5 3.3 3.8 l1.2 -1.5 l3 1 l0 2.5 q-7.5 1 -9.5 -10 z" fill="none" stroke="#fff" stroke-width="1.1"/>
      <rect x="183" y="427" width="20" height="20" fill="var(--navy)"/>
      <rect x="187" y="432" width="12" height="9" fill="none" stroke="#fff" stroke-width="1.1"/>
      <path d="M187 432 l6 5 l6 -5" fill="none" stroke="#fff" stroke-width="1.1"/>
      <rect x="212" y="427" width="20" height="20" fill="var(--navy)"/>
      <circle cx="222" cy="437" r="6" fill="none" stroke="#fff" stroke-width="1.1"/>
      <ellipse cx="222" cy="437" rx="2.6" ry="6" fill="none" stroke="#fff" stroke-width="1"/>
      <path d="M216 437 h12 M217 434 h10 M217 440 h10" stroke="#fff" stroke-width="0.9"/>
    </svg>

    <div class="contact">
      <div>470-555-0184</div>
      <div>info@klvplantservices.com</div>
      <div>www.klvplantservices.com</div>
    </div>

    <div class="divider"></div>

    <div class="address">
      2950 Orchard Ridge Rd Lakeview<br>Hollow, GA 30418
    </div>
  </section>

  <section class="card card--back" role="img" aria-label="Business card back: navy field with repeated faint company name pattern and centred company name">
    <div class="brand">KLV<br>Plant Services</div>
  </section>

</body>
</html>
```